R7M Horizon Business Card Design

We need a business card created for our New Business "R7M Horizon"<br/><br/>The business card design is up to you however the following information must be on the business card:<br/><br/>Front of the business card -<br/>Email :darrenp@r7mhorizon.nz<br/>Mobile: +64 (0) 22 4870 619<br/>Website: www.r7mhorizon.nz<br/>Card Owner Name: Darren Paltrow<br/>Company Title: Business Development Manager<br/>Slogan: "The BEST of both worlds". <br/>Logo On the front attached to the design brief<br/><br/>On the back: <br/>Space on the back for 4 more versions of the logo across the bottom of the card indicating different subsidiary brands - R7M Coffee, R7M Arts, R7M ?? (The card will be used for all of these brands - We Will add the extra subsidiary logos to the design once the design is finished (We are a graphics design team). <br/><br/>Other than that we want a premium feeling logo that remains universally usable depending on the business entity that we are using the card for. The use of bright bold colours would be great but we still want the card to feel premium.
Target Market(s)
Gift Design and Manufacturing Companies
Contact Information for Business Card
Front of the business card -
Email :darrenp@r7mhorizon.nz
Mobile: +64 (0) 22 4870 619
Website: www.r7mhorizon.nz
Card Owner Name: Darren Paltrow
Company Title: Business Development Manager
Slogan: "The BEST of both worlds".
Logo On the front attached to the design brief

```html
<!DOCTYPE html>
<html lang="en">
<head>
<meta charset="utf-8">
<title>R7M Horizon Business Card</title>
<link href="https://fonts.googleapis.com/css2?family=Montserrat:wght@400;600;700;800&family=Arimo:wght@400&display=swap" rel="stylesheet">
<style>
  :root {
    --brand-blue: #3547a0;
    --ink: #1f1f24;
    --paper: #ffffff;
    --divider: #b9bcc4;
    --backdrop: #e9eaee;
  }
  * { box-sizing: border-box; margin: 0; padding: 0; }
  html, body { width: 1200px; height: 1015px; overflow: hidden; }
  body {
    background: var(--backdrop);
    font-family: "Montserrat", Arial, sans-serif;
    display: flex;
    flex-direction: column;
    align-items: center;
    justify-content: center;
    gap: 60px;
  }
  .card {
    width: 740px;
    height: 423px;
    position: relative;
    overflow: hidden;
    box-shadow: 0 10px 28px rgba(0,0,0,0.18);
  }
  .card-back {
    background: var(--brand-blue);
    display: flex;
    align-items: center;
    justify-content: center;
  }
  .wordmark {
    font-weight: 800;
    letter-spacing: 1px;
    white-space: nowrap;
  }
  .card-back .wordmark { color: var(--paper); font-size: 54px; }

  .card-front { background: var(--paper); }
  .front-body {
    position: absolute;
    left: 0; right: 0; top: 0;
    height: 330px;
    display: flex;
    align-items: center;
    padding-left: 56px;
  }
  .card-front .wordmark { color: var(--brand-blue); font-size: 32px; width: 300px; }
  .front-divider {
    width: 1px;
    height: 150px;
    background: var(--divider);
    margin: 0 30px 0 10px;
  }
  .contact-name {
    color: var(--brand-blue);
    font-weight: 800;
    font-size: 22px;
    text-transform: uppercase;
    letter-spacing: 0.3px;
  }
  .contact-title {
    font-family: "Arimo", Arial, sans-serif;
    font-size: 17px;
    color: var(--ink);
    margin: 2px 0 12px;
  }
  .contact-list { list-style: none; }
  .contact-list li {
    display: flex;
    align-items: center;
    gap: 8px;
    font-family: "Arimo", Arial, sans-serif;
    font-size: 16px;
    color: var(--ink);
    line-height: 24px;
  }
  .contact-list svg { width: 17px; height: 17px; flex: none; }
  .web-domain { color: var(--brand-blue); }
  .slogan-band {
    position: absolute;
    left: 0; right: 0; bottom: 0;
    height: 93px;
    background: var(--brand-blue);
    display: flex;
    align-items: center;
    padding-left: 222px;
  }
  .slogan {
    color: var(--paper);
    font-weight: 800;
    font-size: 19px;
    letter-spacing: 2.2px;
    text-transform: uppercase;
  }
</style>
</head>
<body>
  <section class="card card-back" aria-label="Card back">
    <div class="wordmark">R7M Horizon</div>
  </section>

  <section class="card card-front" aria-label="Card front">
    <div class="front-body">
      <div class="wordmark">R7M Horizon</div>
      <div class="front-divider"></div>
      <div class="contact">
        <h1 class="contact-name">Darren Paltrow</h1>
        <p class="contact-title">Business Development Manager</p>
        <ul class="contact-list">
          <li>
            <svg viewBox="0 0 16 16" aria-hidden="true"><rect x="0.75" y="0.75" width="14.5" height="14.5" rx="2" fill="none" stroke="#3547a0" stroke-width="1.5"/><path d="M5 3.5l1.6 2.3-1 1c.6 1.3 1.6 2.3 2.9 2.9l1-1 2.3 1.6-.8 1.6c-3.6-.3-6.7-3.4-7-7z" fill="#3547a0"/></svg>
            +64 (0) 22 4870 619
          </li>
          <li>
            <svg viewBox="0 0 16 16" aria-hidden="true"><rect x="0.5" y="3" width="15" height="10" fill="#3547a0"/><path d="M1 3.5l7 5 7-5" fill="none" stroke="#fff" stroke-width="1.2"/></svg>
            darrenp@r7mhorizon.nz
          </li>
          <li>
            <svg viewBox="0 0 16 16" aria-hidden="true"><circle cx="8" cy="8" r="7" fill="none" stroke="#3547a0" stroke-width="1.5"/><ellipse cx="8" cy="8" rx="3" ry="7" fill="none" stroke="#3547a0" stroke-width="1.2"/><path d="M1 8h14M2.5 4.5h11M2.5 11.5h11" stroke="#3547a0" stroke-width="1.1"/></svg>
            <span>www.<span class="web-domain">r7mhorizon</span>.nz</span>
          </li>
        </ul>
      </div>
    </div>
    <div class="slogan-band">
      <p class="slogan">The Best of Both Worlds</p>
    </div>
  </section>
</body>
</html>
```